BrindleStaffing Business Card Design

We are a staffing company finding positions for dedicated nurses and physicians.

Target Market(s)

Business Professionals

Industry/Entity Type

Staffing

Contact Information for Business Card

Gordon Pratley
Chairman
417 39th Avenue South
SAINT PETERSBURG FL 33712
813-555-4172 Mobile
813-555-8036 Fax
gpratley@brindlestaffing.com
www.brindlestaffing.com

Font styles to use
Sans Serif

Colors
fbee3e
f04a50
f37122

Requirements
Must have
• Logo Attached, see colors below. We'd like to see Yellow, Orange and Red.

```html
<!DOCTYPE html>
<html lang="en">
<head>
<meta charset="utf-8">
<title>BrindleStaffing Business Card</title>
<link rel="stylesheet" href="https://fonts.googleapis.com/css2?family=Source+Sans+3:wght@400;600;700&display=swap">
<style>
  :root {
    --backdrop: #1f1f1f;
    --brand-yellow: #fbee3e;
    --brand-red: #f04a50;
    --brand-orange: #f37122;
    --ink: #222222;
    --paper: #ffffff;
    --card-w: 540px;
    --card-h: 310px;
  }
  * { box-sizing: border-box; margin: 0; padding: 0; }
  html, body {
    width: 1200px;
    height: 960px;
    overflow: hidden;
    background: var(--backdrop);
    font-family: "Source Sans 3", "Myriad Pro", Arial, sans-serif;
  }
  .canvas { position: relative; width: 1200px; height: 960px; }
  .card {
    position: absolute;
    width: var(--card-w);
    height: var(--card-h);
    box-shadow: 0 10px 30px rgba(0,0,0,0.45);
  }
  .card-front {
    left: 600px;
    top: 140px;
    background: var(--brand-orange);
    color: var(--paper);
    display: flex;
    flex-direction: column;
    align-items: center;
    justify-content: center;
    gap: 14px;
  }
  .card-front .brand-name {
    font-size: 50px;
    font-weight: 700;
    letter-spacing: -0.5px;
    color: var(--paper);
  }
  .card-front .web-address {
    font-size: 17px;
    letter-spacing: 2px;
    color: var(--brand-yellow);
  }
  .card-back {
    left: 120px;
    top: 500px;
    background: var(--paper);
    color: var(--ink);
  }
  .person { position: absolute; left: 34px; top: 28px; }
  .person-name { font-size: 21px; font-weight: 700; color: var(--brand-red); line-height: 1.1; }
  .person-title { font-size: 17px; color: var(--brand-orange); line-height: 1.2; }
  .card-back .brand-name {
    position: absolute;
    right: 34px;
    top: 86px;
    font-size: 38px;
    font-weight: 700;
    letter-spacing: -0.5px;
    color: var(--brand-red);
  }
  .contact { position: absolute; left: 34px; top: 146px; font-size: 15px; line-height: 1.35; }
  .address { margin-bottom: 10px; }
  .contact-list { list-style: none; }
  .contact-list li { display: flex; align-items: center; gap: 8px; }
  .contact-list svg { width: 13px; height: 13px; flex: none; }
  .contact-label { color: var(--brand-orange); font-weight: 600; }
</style>
</head>
<body>
<main class="canvas">
  <section class="card card-front" aria-label="Card front">
    <div class="brand-name">BrindleStaffing</div>
    <div class="web-address">www.brindlestaffing.com</div>
  </section>

  <section class="card card-back" aria-label="Card back">
    <div class="person">
      <div class="person-name">Gordon Pratley</div>
      <div class="person-title">Chairman</div>
    </div>
    <div class="brand-name">BrindleStaffing</div>
    <div class="contact">
      <p class="address">417 39th Avenue South<br>Saint Petersburg FL 33712</p>
      <ul class="contact-list">
        <li>
          <svg viewBox="0 0 16 16" aria-hidden="true"><circle cx="8" cy="8" r="8" fill="var(--brand-orange)"/><path d="M5 4.5c.6-.4 1.2-.3 1.5.3l.6 1.2c.2.4 0 .8-.3 1.1l-.4.3c.4 1 1.2 1.8 2.2 2.2l.3-.4c.3-.3.7-.5 1.1-.3l1.2.6c.6.3.7.9.3 1.5-.5.7-1.4 1-2.3.7C7.1 11 5 8.9 4.3 6.8c-.3-.9 0-1.8.7-2.3z" fill="#fff"/></svg>
          <span>813-555-4172 <span class="contact-label">Mobile</span></span>
        </li>
        <li>
          <svg viewBox="0 0 16 16" aria-hidden="true"><circle cx="8" cy="8" r="8" fill="var(--brand-orange)"/><rect x="5.5" y="3.8" width="5" height="3" fill="#fff"/><rect x="4" y="6.6" width="8" height="3.8" rx=".6" fill="#fff"/><rect x="5.5" y="9.4" width="5" height="2.8" fill="#fff" stroke="var(--brand-orange)" stroke-width=".6"/></svg>
          <span>813-555-8036 <span class="contact-label">Fax</span></span>
        </li>
        <li>
          <svg viewBox="0 0 16 16" aria-hidden="true"><circle cx="8" cy="8" r="8" fill="var(--brand-orange)"/><rect x="4" y="5.2" width="8" height="5.6" rx=".6" fill="#fff"/><path d="M4.3 5.6 8 8.4l3.7-2.8" fill="none" stroke="var(--brand-orange)" stroke-width=".9"/></svg>
          <span>gpratley@brindlestaffing.com</span>
        </li>
        <li>
          <svg viewBox="0 0 16 16" aria-hidden="true"><circle cx="8" cy="8" r="7.5" fill="var(--brand-orange)"/><g fill="none" stroke="#fff" stroke-width=".9"><circle cx="8" cy="8" r="4.5"/><ellipse cx="8" cy="8" rx="2" ry="4.5"/><path d="M3.5 8h9"/></g></svg>
          <span>www.brindlestaffing.com</span>
        </li>
      </ul>
    </div>
  </section>
</main>
</body>
</html>
```